CREATE A KILLER WEBSITE DESIGN

We are a firearms training company that trains CIVILIANS (no police or military pictures - thank you!) to defend themselves and are looking for a killer design that's clean, easy to navigate and modern! We want the newest trends applied to this sight like a scrollable site so you can scroll down and see all the features. We are okay with tweaking the HTML but need the artistic design to look good. I'll provide a link to our current site along with a sight we really like so you can get an idea!

I'm supplying a PowerPoint Design we are going with from another designer so you can match the style to the new site.

PAGES: (Please use information from our current site. We like the information but just want a more polished look similar to the NWDPA site below but in our colors.)
Home - Long Form Scrolling Site. Top fold will be a video with a play button.
Harbor Institute - Seven Level Training Program Info Page That Will Contain A Video.
Contact Us - This will be a page that DOES NOT CONTAIN AN EMAIL ADDRESS. Just a contact us form
Meet The Trainer: Dennis Pollock

Our site:
https://www.brightmeadowskills.biz

Sights We Like:
https://www.nwdefenseplanners.com
https://quorvel.com
https://lindenplatecorp.com
https://www.velbrookgear.com

Target Market(s)

Men and women ages 21 to 100 years old

Industry/Entity Type

Self Defense

Number of Pages Required

5+ page

Font styles to use
Sans Serif

Colors
f26267

Requirements
Must have
• Clean and engaging. Use of colors that match our logo.
Should not have
• Poor design quality

```html
<!DOCTYPE html>
<html lang="en">
<head>
<meta charset="utf-8">
<title>Harbor Institute</title>
<link href="https://fonts.googleapis.com/css2?family=Audiowide&family=Poppins:ital,wght@0,400;0,500;0,600;1,400;1,500&display=swap" rel="stylesheet">
<style>
:root{
  --red:#e31f26;
  --red-soft:#ec4a50;
  --black:#000;
  --ink:#1c1c1c;
  --white:#fff;
  --muted:#555;
  --display:"Audiowide",sans-serif;
  --body:"Poppins",sans-serif;
}
*{margin:0;padding:0;box-sizing:border-box}
html,body{width:1200px;height:4121px;overflow:hidden}
body{position:relative;background:var(--white);font-family:var(--body);color:var(--ink)}
.abs{position:absolute}
.section{position:absolute;left:0;width:1200px;overflow:hidden}
.display{font-family:var(--display);text-transform:uppercase;letter-spacing:1px;line-height:1.2}

/* hero */
.hero{top:0;height:700px}
.hero svg{position:absolute;left:0;top:0}
.brand{left:173px;top:62px;display:flex;align-items:center;gap:12px;color:var(--white);font-family:var(--body);font-weight:600;font-size:20px;letter-spacing:2px}
.brand-dot{width:26px;height:26px;border-radius:50%;background:var(--red)}
.hero-title{left:173px;top:280px;color:var(--white);font-size:50px}

/* instructor */
.instructor{top:640px;height:660px;background:var(--red)}
.instructor svg{position:absolute;left:0;top:0}
.eyebrow{font-size:15px;text-transform:uppercase}
.instructor .eyebrow{left:611px;top:122px;color:var(--white)}
.instructor h2{left:611px;top:150px;color:var(--white);font-size:34px}
.instructor p{left:611px;top:218px;width:418px;color:var(--white);font-size:13px;line-height:24.6px;text-align:justify}
.btn-light{left:611px;top:443px;width:152px;height:61px;background:var(--white);border-radius:8px;color:var(--ink);font-family:var(--display);font-size:15px;text-transform:uppercase;display:flex;align-items:center;justify-content:center}

/* levels */
.levels{top:1300px;height:913px;background:var(--white)}
.levels .eyebrow{left:0;width:1200px;top:88px;text-align:center}
.levels h2{left:0;width:1200px;top:122px;text-align:center;color:var(--red);font-size:35px}
.levels .intro{left:175px;width:850px;top:183px;text-align:center;font-size:13px;line-height:25px}
.level{width:270px}
.level .num{font-family:var(--display);font-size:150px;line-height:1;height:170px}
.level h3{font-family:var(--display);font-size:18px;line-height:24px;text-transform:uppercase;margin-top:-8px}
.level p{font-size:11.5px;line-height:20px;color:var(--muted);margin-top:12px;width:200px}
.is-red .num,.is-red h3{color:var(--red)}
.arrow{width:34px;height:60px}

/* stories */
.stories{top:2213px;height:640px;background:var(--black)}
.stories svg{position:absolute;left:0;top:0}
.stories .eyebrow{left:654px;top:136px;color:var(--white)}
.stories h2{left:654px;top:168px;color:var(--white);font-size:36px;line-height:45px}
.quote{left:654px;top:270px;width:380px;color:var(--white);font-style:italic;font-size:13px;line-height:27px}
.author{left:654px;top:380px;color:var(--white);font-style:italic;font-weight:500;font-size:19px}
.date{left:654px;top:412px;color:var(--white);font-style:italic;font-size:13px}

/* products */
.products{top:2853px;height:667px;background:var(--red)}
.products .eyebrow{left:0;width:1200px;top:76px;text-align:center;color:var(--white)}
.products h2{left:0;width:1200px;top:104px;text-align:center;color:var(--white);font-size:35px}
.card{top:211px;width:268px;height:328px;background:var(--white);border-radius:8px;box-shadow:0 6px 16px rgba(0,0,0,.18)}
.card .shot{position:absolute;left:34px;top:30px;width:200px;height:118px;border-radius:4px}
.card h3{position:absolute;left:14px;width:240px;top:176px;text-align:center;font-weight:400;font-size:17px;line-height:25px;text-transform:uppercase}
.price{position:absolute;left:74px;top:243px;width:120px;height:47px;background:var(--red);border-radius:6px;color:var(--white);font-family:var(--display);font-size:19px;display:flex;align-items:center;justify-content:center}

/* contact */
.contact{top:3520px;height:544px;background:linear-gradient(180deg,#1b1b1b,#101010 60%,#1a1a1a)}
.contact h2{color:var(--white);font-size:26px}
.field{left:173px;width:379px;height:48px;background:var(--white);font-size:15px;padding:13px 10px;color:var(--ink)}
.send{left:173px;top:426px;width:117px;height:46px;background:var(--red);color:var(--white);font-family:var(--display);font-size:17px;text-transform:uppercase;display:flex;align-items:center;justify-content:center}
.role{left:632px;top:134px;width:400px;color:var(--white);font-size:14px;line-height:22px;text-align:justify;text-transform:uppercase}
.info{left:635px;display:flex;gap:18px;align-items:center;color:var(--white);font-size:15px;line-height:22px}
.info svg{flex:none}

/* footer */
.footer{top:4064px;height:57px;background:var(--red);color:var(--white);font-size:13px;display:flex;align-items:center;justify-content:center}
</style>
</head>
<body>

<section class="section hero">
  <svg width="1200" height="700" viewBox="0 0 1200 700">
    <rect width="1200" height="700" fill="#000"/>
    <path d="M0 600 C150 545 300 520 460 548 C640 580 760 660 930 650 C1060 640 1140 600 1200 570 V700 H0 Z" fill="#e31f26"/>
    <circle cx="985" cy="250" r="410" fill="#e31f26"/>
    <path d="M560 640 C760 690 1000 690 1200 590 V640 C1000 720 760 715 560 640 Z" fill="#000"/>
    <circle cx="985" cy="255" r="385" fill="#000"/>
    <circle cx="990" cy="250" r="378" fill="#6d7060" role="img" aria-label="Video still of a civilian student firing at steel targets on an outdoor range"/>
    <circle cx="962" cy="307" r="42" fill="none" stroke="#fff" stroke-width="6"/>
    <path d="M948 282 L986 307 L948 332 Z" fill="none" stroke="#fff" stroke-width="6" stroke-linejoin="round"/>
  </svg>
  <div class="abs brand"><span class="brand-dot"></span>HARBOR INSTITUTE</div>
  <h1 class="abs display hero-title">Harbor<br>Institute</h1>
</section>

<section class="section instructor">
  <svg width="1200" height="660" viewBox="0 0 1200 660">
    <rect x="32" y="64" width="528" height="456" rx="6" fill="#ec4a50" role="img" aria-label="Decorative brand backdrop behind the instructor portrait"/>
    <circle cx="298" cy="368" r="163" fill="#000"/>
    <circle cx="298" cy="368" r="157" fill="#9a9a9a" role="img" aria-label="Portrait of instructor Dennis Pollock"/>
  </svg>
  <div class="abs eyebrow">About the instructor</div>
  <h2 class="abs display">Dennis Pollock</h2>
  <p class="abs">Dennis Pollock is a 3rd generation Bayport native and delighted to be a part of this great community. He is a true security expert with 25 years of experience in the security industry. He has appeared on Channel 4, Metro 7, Bay 9 &amp; City Wire news outlets. He has been featured in numerous publications and has trained thousands to protect themselves and their homes from thugs and thieves. He is certified by both the CSTA &amp; the NWDPA as a firearms instructor.</p>
  <div class="abs btn-light">Read more</div>
</section>

<section class="section levels">
  <div class="abs eyebrow">Our 7 levels of training take you</div>
  <h2 class="abs display">From zero to hero</h2>
  <p class="abs intro">Wanna hear something funny? Guess what the average person asks about a concealed weapons class? “How much is it and how long is it?” Can you believe it? We are talking about preparing you for life and death situations and the main concern is “How Fast” and “How Cheap?” WOW!</p>

  <svg class="abs arrow" style="left:60px;top:562px" viewBox="0 0 34 60"><path d="M30 4 L4 30 L30 56" fill="none" stroke="#1c1c1c" stroke-width="2.5"/></svg>
  <svg class="abs arrow" style="left:1096px;top:562px" viewBox="0 0 34 60"><path d="M4 4 L30 30 L4 56" fill="none" stroke="#1c1c1c" stroke-width="2.5"/></svg>

  <div class="abs level" style="left:173px;top:290px"><div class="num">1</div><h3>Concealed<br>carry class</h3><p>Guess what the average person asks about a concealed weap ons class.</p></div>
  <div class="abs level is-red" style="left:469px;top:290px"><div class="num">2</div><h3>Dynamic defensive<br>shooting</h3><p>Guess what the average person asks about a concealed weap ons class.</p></div>
  <div class="abs level" style="left:797px;top:290px"><div class="num">3</div><h3>Fine tuning your<br>technique</h3><p>Guess what the average person asks about a concealed weap ons class.</p></div>
  <div class="abs level is-red" style="left:173px;top:578px"><div class="num">4</div><h3>Virtual threat<br>-lab</h3><p>Guess what the average person asks about a concealed weap ons class.</p></div>
  <div class="abs level" style="left:469px;top:578px"><div class="num">5</div><h3>Tactical skills<br>&amp; drills</h3><p>Guess what the average person asks about a concealed weap ons class.</p></div>
  <div class="abs level is-red" style="left:797px;top:578px"><div class="num">6</div><h3>Close quarters<br>defense</h3><p>Guess what the average person asks about a concealed weap ons class.</p></div>
</section>

<section class="section stories">
  <svg width="1200" height="640" viewBox="0 0 1200 640">
    <path d="M0 0 H590 C650 150 620 420 500 540 C400 620 180 625 0 585 Z" fill="#e31f26"/>
    <path d="M0 0 H560 C615 150 590 400 475 515 C380 595 170 600 0 560 Z" fill="#3a3a3a" role="img" aria-label="Photo of a rifle, a handgun and brass cartridges on a dark surface"/>
    <path d="M0 640 V610 C300 660 520 560 760 560 C960 560 1080 570 1200 520 V640 Z" fill="#e31f26"/>
    <path d="M995 165 L1025 195 L995 225" fill="none" stroke="#fff" stroke-width="2.5"/>
  </svg>
  <div class="abs eyebrow">Our</div>
  <h2 class="abs display">Success<br>stories</h2>
  <p class="abs quote">“I had never held a gun when I took the Steady Hand Carry class and I’m hooked! I’m going all the way to level 7! Thank you Steady Hand Carry!</p>
  <div class="abs author">Marisa K.</div>
  <div class="abs date">October 14, 2017</div>
</section>

<section class="section products">
  <div class="abs eyebrow">Our</div>
  <h2 class="abs display">Shopping products</h2>
  <div class="abs card" style="left:173px">
    <div class="shot" style="background:linear-gradient(160deg,#5a5a5a,#1e1e1e)" role="img" aria-label="Product photo of a personal handgun safe"></div>
    <h3>Personal handgun safe</h3>
    <div class="price">$89.95</div>
  </div>
  <div class="abs card" style="left:466px">
    <div class="shot" style="background:linear-gradient(160deg,#5d6b46,#2f3a24)" role="img" aria-label="Product photo of a green multi fit holster"></div>
    <h3>Multi fit holster (fits 150 different guns!)</h3>
    <div class="price">$39.95</div>
  </div>
  <div class="abs card" style="left:758px">
    <div class="shot" style="background:linear-gradient(180deg,#6b5a7a,#2a2a2a 55%,#4a5a70)" role="img" aria-label="Product photo of a covert concealment holster worn at the waist"></div>
    <h3>Covert concealment holster</h3>
    <div class="price">$39.95</div>
  </div>
</section>

<section class="section contact" aria-label="Contact">
  <h2 class="abs display" style="left:173px;top:88px">Get in touch</h2>
  <div class="abs field" style="top:139px">Name*</div>
  <div class="abs field" style="top:200px">Email*</div>
  <div class="abs field" style="top:259px">Phone</div>
  <div class="abs field" style="top:318px;height:85px">Message</div>
  <div class="abs send">Send</div>

  <h2 class="abs display" style="left:635px;top:88px">Dennis Pollock</h2>
  <p class="abs role">CSTA firearms instructor, NWDPA instructor &amp; training counsellor, news correspondent, and security expert</p>
  <div class="abs info" style="top:240px">
    <svg width="34" height="40" viewBox="0 0 34 40"><path d="M17 38 C17 38 3 22 3 15 A14 14 0 0 1 31 15 C31 22 17 38 17 38 Z" fill="none" stroke="#fff" stroke-width="2.2"/><circle cx="17" cy="15" r="5" fill="none" stroke="#fff" stroke-width="2.2"/></svg>
    <div>P.O. Box 4120<br>Cedar Point, FL 32099</div>
  </div>
  <div class="abs info" style="top:308px">
    <svg width="34" height="36" viewBox="0 0 34 36"><path d="M8 3 L14 11 L10 15 C12 21 15 24 21 26 L25 22 L33 28 L28 34 C16 33 3 20 2 8 Z" fill="none" stroke="#fff" stroke-width="2.2" stroke-linejoin="round"/></svg>
    <div>LOCAL: 555-010-4HBR (4427)<br>TOLL-FREE: 800-555-0199</div>
  </div>
  <div class="abs info" style="top:382px">
    <svg width="34" height="26" viewBox="0 0 34 26"><rect x="2" y="2" width="30" height="22" fill="none" stroke="#fff" stroke-width="2.2"/><path d="M2 2 L17 15 L32 2" fill="none" stroke="#fff" stroke-width="2.2"/></svg>
    <div>hello@harborinstitute.example</div>
  </div>
</section>

<footer class="section footer">Copyrights @ Harbor Institute 2021 - All Rights Reserved.</footer>

</body>
</html>
```